Redesign Canvas Art E-Commerce Website

Help! I hired a couple of companies on Brisklo.com to build and design an e-commerce website for me. After three long and painful months, I have one that I believe is functional on the back-end, but aesthetically on the front end is a mess.

We are a small family business that will take your digital photo and manipulate it into a digitally created oil, watercolor or impressionist style pieces of artwork that we print on museum quality, gallery grade canvas and ship to the customer, ready to hang.

We are looking to create an e-commerce website where a customer can choose their art style, upload a photo, choose their canvas size and orientation (horizontal or vertical) and checkout. Within 48 hours, we will send them back a proof of their newly created, customized artwork for them to approve or not approve. If they approve, we print, package and ship them the product. If they do not approve, we offer unlimited revisions until they are happy.

As I mentioned, the back end functionality is already there, just need design help. No coding required

Here is a link to the development page that they created: https://plumwickstudio.com/development/

As you can see, it looks off...doesnt line up properly, wasted space, weird font. Feel free to either correct the homepage they created or design an entirely new page. I am attaching some examples of before and after photos of artwork for reference. I also think the testimonials page and shop page can use a little style. The content is there and accurate, it just doesn't look pretty. Please keep in mind that our customers will probably not be very tech savvy. The customers will probably be sending us pics of kids, grandkids, pets, family portraits, vacation photos, etc.

Here is one of our competitors - www.gildavantry.com
Their website looks clean and inviting.

Thank you in advance! Im looking forward to seeing the results. I am including our logo in the attachments (I do not have it in a vector file, just a jpeg)

Target Market(s)

Non tech-savvy indiduals, 30-70 years old

Industry/Entity Type

Please look at https://plumwickstudio.com/development/ to see various pages and what the other designers did

Number of Pages Required

1 page

Requirements
Must have
• Verbiage on pages leave "as is" but feel free to change styles. Would like to keep existing four categories on homepage
Nice to have
• Warm and inviting homepage that evokes emotion

```html
<!DOCTYPE html>
<html lang="en">
<head>
<meta charset="utf-8">
<title>Easel Haven – Turn Your Digital Photos Into Wall Art</title>
<link href="https://fonts.googleapis.com/css2?family=Audiowide&family=Lato:wght@300;400;700&display=swap" rel="stylesheet">
<style>
:root{
  --red:#e5350e;
  --blue:#2aaed3;
  --ink:#1c1c1c;
  --text:#3a3a3a;
  --dark:#1b1b1b;
  --card:#f4f4f4;
  --footer-grey:#ececec;
}
*{margin:0;padding:0;box-sizing:border-box}
html,body{width:1200px;height:4227px;overflow:hidden;background:#fff}
body{position:relative;font-family:'Lato',sans-serif;color:var(--text)}
.abs{position:absolute}
.display{font-family:'Audiowide',sans-serif;color:var(--ink);font-weight:400}
.btn{position:absolute;background:var(--red);color:#fff;border-radius:22px;font-size:15px;display:flex;align-items:center;justify-content:center}

/* header */
.site-header{position:absolute;left:0;top:0;width:1200px;height:115px;background:#fff}
.brand{position:absolute;left:90px;top:38px;display:flex;align-items:center;gap:10px;font-size:28px;font-weight:700;color:var(--ink)}
.brand .dot{width:22px;height:22px;border-radius:50%;background:var(--red)}
.nav a{position:absolute;top:52px;font-size:15px;color:var(--ink);text-decoration:none}
.nav a.active{color:var(--red)}
.cart{position:absolute;left:1058px;top:48px}

/* hero */
.hero{position:absolute;left:0;top:115px;width:1200px;height:680px;overflow:hidden}
.hero-visual{position:absolute;left:0;top:0;width:1200px;height:680px;background:linear-gradient(100deg,#f8f8f8 0%,#e7e7e7 50%,#d2d2d2 100%)}
.hero-title{position:absolute;left:113px;top:132px;font-size:40px;line-height:55px}
.hero-title .blue{color:var(--blue)}
.hero-title .red{color:var(--red)}

/* showcase */
.section-title{position:absolute;left:0;width:1200px;text-align:center;font-size:31px;line-height:36px}
.slide-main{position:absolute;left:212px;top:1019px;width:778px;height:435px;border:4px solid var(--blue);border-radius:33px;background:linear-gradient(120deg,#8fc6ea 0%,#b0552a 35%,#7e3a1c 55%,#cfe4f2 85%)}
.slide-thumb{position:absolute;left:714px;top:1343px;width:374px;height:208px;border:4px solid var(--red);border-radius:28px;background:linear-gradient(120deg,#9ccbea 0%,#8c4a22 45%,#2a2a2a 65%,#bfe0f5 100%);box-shadow:0 6px 14px rgba(0,0,0,.2)}
.arrow{position:absolute;width:56px;height:56px;border-radius:50%;background:var(--red);display:flex;align-items:center;justify-content:center}
.dots span{position:absolute;top:1488px;width:12px;height:12px;border-radius:50%;background:#8fd0e6}
.dots span.on{background:var(--red);width:16px;height:16px;top:1486px}

/* categories */
.categories{position:absolute;left:0;top:1776px;width:1200px;height:670px;background:var(--dark)}
.cat{position:absolute;width:230px;height:230px;border-radius:50%;border:8px solid var(--blue)}
.cat-label{position:absolute;width:260px;text-align:center;color:#fff;font-size:26px}

/* about */
.about-title{position:absolute;left:113px;top:2578px;font-size:32px}
.about-copy{position:absolute;left:113px;top:2636px;width:488px;font-size:15.6px;line-height:25.8px;text-align:justify;font-weight:300;color:#2a2a2a}
.photo-big{position:absolute;left:637px;top:2587px;width:468px;height:417px;border:4px solid var(--red);border-radius:16px;background:linear-gradient(135deg,#5f8f3e 0%,#c98a5c 45%,#9fb7cf 75%,#e0e0d8 100%)}
.photo-small{position:absolute;left:809px;top:2876px;width:269px;height:240px;border:4px solid var(--red);border-radius:14px;background:linear-gradient(135deg,#cfd7c6 0%,#b88566 45%,#7e9cb9 80%)}

/* why us */
.card{position:absolute;top:3352px;width:332px;height:474px;background:var(--card);border:1.5px solid #8fd2e6;border-radius:12px;box-shadow:0 4px 10px rgba(0,0,0,.12);text-align:center}
.card svg{position:absolute;left:116px;top:45px}
.card h3{position:absolute;left:0;top:215px;width:100%;font-family:'Audiowide',sans-serif;font-weight:400;font-size:27px;line-height:35px;color:var(--ink)}
.card p{position:absolute;left:28px;width:276px;font-size:16.5px;line-height:29.5px;color:#333}

/* footer */
.footer-band{position:absolute;left:320px;top:4005px;width:880px;height:74px;background:var(--red)}
.footer-links{position:absolute;left:488px;top:4029px;font-size:19px;color:#fff;word-spacing:2px}
.footer-badge{position:absolute;left:89px;top:3923px;width:236px;height:236px;border-radius:50%;background:#ededed}
.footer-badge .name{position:absolute;left:0;top:82px;width:100%;text-align:center;font-size:26px;font-weight:700;color:var(--ink)}
.social{position:absolute;top:4079px;width:20px;height:20px;border-radius:50%;background:#555}
.footer-mail{position:absolute;left:343px;top:4092px;font-size:19px;color:#333;display:flex;align-items:center;gap:12px}
.footer-legal{position:absolute;left:786px;top:4094px;font-size:16.5px;color:#333}
.copyright{position:absolute;left:0;top:4165px;width:1200px;height:62px;background:var(--footer-grey);display:flex;align-items:center;justify-content:center;font-size:14.5px;color:#444}
</style>
</head>
<body>

<header class="site-header">
  <div class="brand"><span class="dot"></span>Easel Haven</div>
  <nav class="nav">
    <a class="active" style="left:396px">Home</a>
    <a style="left:474px">Shop</a>
    <a style="left:545px">Testimonials</a>
    <a style="left:666px">About Us</a>
    <a style="left:767px">FAQs</a>
    <a style="left:839px">My Orders</a>
    <a style="left:946px">Contact Us</a>
  </nav>
  <svg class="cart" width="32" height="30" viewBox="0 0 32 30" aria-label="Cart">
    <path d="M2 6h5l4 13h13l3-9H9" fill="none" stroke="#111" stroke-width="2.6" stroke-linejoin="round"/>
    <path d="M10 10h16l-3 8H12z" fill="#111"/>
    <circle cx="13" cy="24" r="2.4" fill="#111"/><circle cx="23" cy="24" r="2.4" fill="#111"/>
    <circle cx="23" cy="5" r="5" fill="var(--red)"/>
  </svg>
</header>

<section class="hero">
  <div class="hero-visual" role="img" aria-label="Gallery wall with three framed canvas prints of family and wedding portraits"></div>
  <svg class="abs" style="left:0;top:555px" width="1200" height="125" viewBox="0 0 1200 125" aria-hidden="true">
    <path d="M0 125 L0 58 C200 110 420 115 640 98 C880 80 1050 55 1200 45 L1200 125 Z" fill="#fff"/>
    <path d="M0 40 C200 95 420 100 640 83 C880 65 1050 42 1200 30 L1200 44 C1050 56 880 80 640 98 C420 114 200 108 0 58 Z" fill="var(--blue)"/>
  </svg>
  <h1 class="hero-title display">Turn Your <span class="blue">Digital</span><br><span class="blue">Photos</span> Into One<br>of a Kind <span class="red">Wall Art</span></h1>
  <div class="btn" style="left:113px;top:325px;width:173px;height:43px">Get Started</div>
</section>

<h2 class="section-title display" style="top:888px">FROM PHOTO TO MUSEUM<br>QUALITY CANVAS ART</h2>
<div class="slide-main" role="img" aria-label="Painted canvas version of a rider on a brown horse under blue sky"></div>
<div class="slide-thumb" role="img" aria-label="Original photo of a rider jumping a brown horse"></div>
<div class="arrow" style="left:67px;top:1183px"><svg width="16" height="16" viewBox="0 0 16 16"><path d="M10 3 5 8l5 5" fill="none" stroke="#fff" stroke-width="2.2"/></svg></div>
<div class="arrow" style="left:1072px;top:1183px"><svg width="16" height="16" viewBox="0 0 16 16"><path d="M6 3l5 5-5 5" fill="none" stroke="#fff" stroke-width="2.2"/></svg></div>
<div class="dots"><span style="left:554px"></span><span style="left:573px"></span><span class="on" style="left:592px"></span><span style="left:615px"></span><span style="left:633px"></span></div>
<div class="btn" style="left:514px;top:1604px;width:172px;height:42px">Get Started</div>

<section class="categories">
  <h2 class="section-title display" style="top:75px;color:#fff">CATEGORIES</h2>
  <div class="cat" role="img" aria-label="Oil style example of a wedding couple" style="left:115px;top:228px;background:linear-gradient(135deg,#3d6a2a,#b8553f 55%,#e7ded0)"></div>
  <div class="cat-label" style="left:100px;top:478px">Oil</div>
  <div class="cat" role="img" aria-label="Water color style example of a mother and baby" style="left:361px;top:172px;background:linear-gradient(135deg,#fbeee8,#eab9a6 55%,#fff6f2)"></div>
  <div class="cat-label" style="left:346px;top:422px">Water Color</div>
  <div class="cat" role="img" aria-label="Impressionist style example of a bride with bouquet" style="left:609px;top:228px;background:linear-gradient(160deg,#3b2a1f,#c09a72 45%,#eae7da 70%,#7b8a44)"></div>
  <div class="cat-label" style="left:594px;top:478px">Impressionist</div>
  <div class="cat" role="img" aria-label="Digital photo example of two children with ice cream" style="left:857px;top:228px;background:linear-gradient(135deg,#f1e2d3,#d9a98a 45%,#6fb6d9 80%)"></div>
  <div class="cat-label" style="left:850px;top:478px">Digital Photo</div>
  <div class="btn" style="left:514px;top:573px;width:172px;height:43px">Get Started</div>
</section>

<h2 class="about-title display">About Us</h2>
<div class="about-copy">
  <p>At Easel Haven, we take your digital photo and turn it into a one-of-a-kind piece of artwork!</p>
  <p>The process couldn’t be any easier. Simply upload your photo, choose your art style and size, and let our team of skilled digital artists do the rest. Do you want to put your digital photo on canvas without an art style? No problem! Just choose the “Digital Photo/Retouching” category and upload your photo. We can print your photo “as is” or do some minor retouching (e.g. remove objects, enhance colors, lighten photo, etc)</p>
  <p>You will receive a proof in your email to approve within 1-2 days. Once approved, your customized artwork will be transferred to canvas and shipped from our design studio in Florida.</p>
  <p>Easel Haven art makes a great gift for just about any special occasion. Know someone with an upcoming birthday, anniversary, housewarming party, wedding or other event? We’ve got you covered!</p>
  <p>Turn your cherished memories into a customized canvas masterpiece today!</p>
</div>
<div class="photo-big" role="img" aria-label="Painted canvas of a laughing older couple outdoors"></div>
<div class="photo-small" role="img" aria-label="Original photo of the older couple piggyback in a park"></div>

<h2 class="section-title display" style="top:3245px">Why Us?</h2>

<div class="card" style="left:64px">
  <svg width="100" height="130" viewBox="0 0 100 130" aria-hidden="true">
    <g stroke="var(--red)" stroke-width="4" stroke-linecap="round"><path d="M50 2v12M14 18l8 8M86 18l-8 8M2 54h12M86 54h12"/></g>
    <circle cx="50" cy="56" r="30" fill="#ffd23f"/>
    <rect x="35" y="82" width="30" height="28" rx="3" fill="#ffc21a"/>
    <rect x="33" y="95" width="34" height="6" fill="#2f3b4c"/><rect x="33" y="105" width="34" height="6" fill="#2f3b4c"/>
    <rect x="40" y="113" width="20" height="8" rx="3" fill="#2f3b4c"/>
  </svg>
  <h3>Your Idea Your<br>Design</h3>
  <p style="top:300px">Each art piece is customized for you! You choose your size, orientation and art style. Makes a perfect gift!!!</p>
</div>

<div class="card" style="left:435px">
  <svg width="100" height="130" viewBox="0 0 100 130" aria-hidden="true">
    <rect x="20" y="62" width="56" height="34" rx="3" fill="var(--red)"/>
    <path d="M76 72h14l10 14v10H76z" fill="#f39b1f"/>
    <g stroke="#f4b14a" stroke-width="3"><path d="M0 70h14M4 80h12M8 90h10"/></g>
    <circle cx="34" cy="100" r="8" fill="#2f3b4c"/><circle cx="84" cy="100" r="8" fill="#2f3b4c"/>
    <circle cx="34" cy="48" r="22" fill="#fff" stroke="#2f3b4c" stroke-width="4"/>
    <path d="M34 34v14l9 6" fill="none" stroke="var(--red)" stroke-width="3"/>
  </svg>
  <h3 style="top:228px">Fast Shipping</h3>
  <p style="top:300px">Your artwork is printed and shipped in the USA! We offer fast turnaround with transit times typically 3-7 days. Free tracking with each order!!</p>
</div>

<div class="card" style="left:806px">
  <svg width="100" height="130" viewBox="0 0 100 130" aria-hidden="true">
    <path d="M30 70l-12 42 14-6 10 12 10-40zM70 70l12 42-14-6-10 12-10-40z" fill="var(--red)"/>
    <circle cx="50" cy="48" r="38" fill="#f5a623"/>
    <circle cx="50" cy="48" r="26" fill="var(--red)"/>
    <path d="M38 48l9 9 16-17" fill="none" stroke="#fff" stroke-width="6" stroke-linecap="round"/>
  </svg>
  <h3 style="top:228px">High Quality</h3>
  <p style="top:300px">We’ve put a lot of effort ensuring your artwork is of the highest quality. Each piece is printed on the highest quality, gallery grade canvas. It is ready to hang upon arrival.!</p>
</div>

<footer>
  <div class="footer-band"></div>
  <div class="footer-badge">
    <div class="name">Easel Haven</div>
  </div>
  <span class="social" style="left:150px"></span>
  <span class="social" style="left:182px"></span>
  <span class="social" style="left:213px"></span>
  <span class="social" style="left:244px"></span>
  <div class="footer-links">About Us &nbsp;|&nbsp;&nbsp; My Orders &nbsp;|&nbsp;&nbsp; Testimonials &nbsp;&nbsp;|&nbsp; Get Started &nbsp;&nbsp;|&nbsp;&nbsp; FAQs</div>
  <div class="footer-mail">
    <svg width="18" height="13" viewBox="0 0 18 13"><rect width="18" height="13" rx="1.5" fill="var(--blue)"/><path d="M1 1.5l8 6 8-6" fill="none" stroke="#fff" stroke-width="1.6"/></svg>
    info@easelhavenart.com
  </div>
  <div class="footer-legal">Privacy Policy &nbsp;|&nbsp; Terms and Conditions</div>
  <div class="copyright">© Copyrights 2023 Easel Haven | All Rights Reserved</div>
</footer>

</body>
</html>
```